Real Estate Business Card

On the front side I want to have my info, my brokerage info.
On the back side I want have my complany’s logo, website and Facebook link. I will provide all this once I select a design.

I would like to see Black background and gold text, Dark Blue and gold text and White and blue text designs

Font styles to use
Sans Serif
Script

```html
<!DOCTYPE html>
<html lang="en">
<head>
<meta charset="UTF-8">
<title>Northgate Real Estate – Business Card</title>
<link rel="stylesheet" href="https://fonts.googleapis.com/css2?family=Montserrat:wght@600;700;800&display=swap">
<style>
  :root {
    --backdrop: #e4e4e4;
    --card: #1c1c1e;
    --gold: #e9c24d;
    --white: #f4f4f4;
    --slate: #4d505b;
    --accent-red: #b5292b;
  }
  html, body {
    margin: 0;
    padding: 0;
    width: 1125px;
    height: 1200px;
    overflow: hidden;
    background: var(--backdrop);
    font-family: "Montserrat", Arial, sans-serif;
  }
  .canvas {
    position: relative;
    width: 1125px;
    height: 1200px;
  }
  .card {
    position: absolute;
    left: 150px;
    width: 826px;
    height: 471px;
    background: var(--card);
    color: var(--white);
    text-align: center;
  }
  .card--front { top: 98px; }
  .card--back { top: 631px; }

  .contact {
    position: absolute;
    left: 0;
    right: 0;
    top: 148px;
  }
  .contact__name {
    margin: 0;
    font-size: 28px;
    font-weight: 700;
    color: var(--gold);
    letter-spacing: 0.5px;
    line-height: 1.1;
  }
  .contact__title {
    margin: 2px 0 0;
    font-size: 19px;
    font-weight: 700;
    color: var(--gold);
    letter-spacing: 0.5px;
  }
  .contact__address {
    margin: 22px 0 0;
    font-size: 18px;
    font-weight: 700;
    line-height: 1.4;
    letter-spacing: 0.4px;
    font-style: normal;
  }
  .contact__lines {
    margin: 14px 0 0;
    font-size: 17px;
    font-weight: 700;
    line-height: 1.55;
    letter-spacing: 0.4px;
  }
  .contact__web {
    letter-spacing: 4px;
  }

  .brand {
    position: absolute;
    left: 0;
    right: 0;
    top: 112px;
    display: flex;
    flex-direction: column;
    align-items: center;
  }
  .brand__square {
    width: 120px;
    height: 120px;
    background: var(--accent-red);
  }
  .brand__name {
    margin: 36px 0 0;
    font-size: 44px;
    font-weight: 800;
    color: var(--slate);
    letter-spacing: 1px;
    text-transform: uppercase;
  }
</style>
</head>
<body>
<main class="canvas">
  <section class="card card--front">
    <div class="contact">
      <h1 class="contact__name">DANIEL REEVE</h1>
      <p class="contact__title">CEO/FOUNDER</p>
      <address class="contact__address">
        4120 HARBOR VIEW ROAD<br>
        JUNEAU, ALASKA 99801
      </address>
      <p class="contact__lines">
        P. 907 555 0148 E . DANIEL@NORTHGATERE.COM<br>
        <span class="contact__web">WWW.NORTHGATERE.COM</span>
      </p>
    </div>
  </section>

  <section class="card card--back">
    <div class="brand">
      <div class="brand__square"></div>
      <p class="brand__name">Northgate Real Estate</p>
    </div>
  </section>
</main>
</body>
</html>
```